Wholesale in Gold Jewellery & Gold Bullion

We are an established gold jewellery and gold bullion wholesaler selling these products to international clients. We already have a name and logo of our company, hence please view attached current card design. We need a completely new design to compliment our business and industry and the final design should be new and elegant.

Contact Information for Business Card

New card details must be same as per current card. Like logo, name, tel no. & etc.

Colors

Designer to choose colors to be used in the design.

```html
<!DOCTYPE html>
<html lang="en">
<head>
<meta charset="UTF-8">
<title>Aurelia &amp; Co Pte Ltd – Business Card</title>
<link rel="stylesheet" href="https://fonts.googleapis.com/css2?family=Montserrat:wght@400;500&family=Playfair+Display:wght@700&display=swap">
<style>
  :root {
    --backdrop: #d9d9d9;
    --card: #ffffff;
    --gold: #c9921f;
    --espresso: #2b2220;
    --ink: #1f1a18;
    --grey: #6b6b6b;
  }
  html, body {
    margin: 0;
    width: 1200px;
    height: 922px;
    overflow: hidden;
    background: var(--backdrop);
  }
  .card {
    position: absolute;
    left: 150px;
    top: 204px;
    width: 900px;
    height: 514px;
    background: var(--card);
    box-shadow: 0 6px 20px rgba(0,0,0,0.18);
    overflow: hidden;
  }
  .brand {
    position: absolute;
    left: 330px;
    top: 70px;
    display: flex;
    align-items: center;
    gap: 22px;
  }
  .brand-dot {
    width: 74px;
    height: 74px;
    border-radius: 50%;
    background: var(--gold);
  }
  .brand-name {
    font-family: "Playfair Display", serif;
    font-weight: 700;
    font-size: 34px;
    letter-spacing: 0.5px;
    color: var(--ink);
  }
  .person {
    position: absolute;
    left: 70px;
    top: 215px;
    width: 330px;
    text-align: right;
    font-family: "Montserrat", sans-serif;
  }
  .person-name {
    font-size: 34px;
    font-weight: 500;
    color: var(--gold);
    line-height: 1.1;
  }
  .person-role {
    font-size: 26px;
    color: var(--grey);
    margin-top: 4px;
  }
  .divider {
    position: absolute;
    left: 430px;
    top: 212px;
    width: 3px;
    height: 120px;
    background: var(--gold);
  }
  .contacts {
    position: absolute;
    left: 460px;
    top: 212px;
    margin: 0;
    padding: 0;
    list-style: none;
    font-family: "Montserrat", sans-serif;
    font-size: 22px;
    color: var(--grey);
  }
  .contacts li {
    display: flex;
    align-items: center;
    gap: 14px;
    height: 32px;
  }
  .contacts svg {
    width: 20px;
    height: 20px;
    fill: none;
    stroke: var(--gold);
    stroke-width: 2;
  }
  .rule {
    position: absolute;
    left: 0;
    right: 0;
    bottom: 82px;
    height: 7px;
    background: var(--gold);
  }
  .band {
    position: absolute;
    left: 0;
    right: 0;
    bottom: 0;
    height: 76px;
    background: var(--espresso);
    display: flex;
    align-items: center;
    padding-left: 60px;
    font-family: "Montserrat", sans-serif;
    font-size: 24px;
    letter-spacing: 1px;
    color: #ffffff;
  }
</style>
</head>
<body>
  <div class="card">
    <div class="brand">
      <div class="brand-dot"></div>
      <div class="brand-name">AURELIA &amp; CO PTE LTD</div>
    </div>

    <div class="person">
      <div class="person-name">Rohan Verakasi</div>
      <div class="person-role">Director</div>
    </div>

    <div class="divider"></div>

    <ul class="contacts">
      <li>
        <svg viewBox="0 0 20 20"><rect x="5" y="1.5" width="10" height="17" rx="2"/><line x1="9" y1="15.5" x2="11" y2="15.5"/></svg>
        +65 9123 4501
      </li>
      <li>
        <svg viewBox="0 0 20 20"><path d="M4 2l4 1 1 4-2 2c1 3 3 5 6 6l2-2 4 1 0 3c0 1-1 2-2 2C9 19 1 11 1 4c0-1 1-2 3-2z"/></svg>
        +65 6555 0180
      </li>
      <li>
        <svg viewBox="0 0 20 20"><rect x="2" y="8" width="16" height="10" rx="1"/><rect x="6" y="2" width="8" height="6"/><line x1="6" y1="13" x2="14" y2="13"/></svg>
        +65 6555 0192
      </li>
      <li>
        <svg viewBox="0 0 20 20"><rect x="1.5" y="4" width="17" height="12" rx="1"/><path d="M1.5 4l8.5 7 8.5-7"/></svg>
        rohan@aureliaco.com
      </li>
    </ul>

    <div class="rule"></div>
    <div class="band">12 Kestrel Lane, Singapore 208851</div>
  </div>
</body>
</html>
```